Podiatry clinic requires a modern revamp and editing of existing website.

I would like a fresh new look and updated information for my current business website. An easy to navigate site with prominent address and phone number for call to action. We are a podiatry clinic that focuses on general and sports podiatry.
I would like 4 pages; including Home page, About Us, Services & Contact.
www.brambleridgepodiatry.net

Target Market(s)

Active working professionals.

Industry/Entity Type

Medical

Coding

Coded - Design and coding required

Number of Pages Required

4 page

Font styles to use
Sans Serif

Colors
6b449b

Requirements
Must have
• A modern look with logo and active images; clean and uncluttered. Visible phone number and address for call to action.
• 4 pages - Home, About Us, Services, Contact.
• Home page - update address & service logos.
• About Us - update of personal information.
• Services - Revamp of existing page.
• Contact page to include Google map, email & phone number.
Nice to have
• Ability to add content easily; eg. a blog or adding video onto Home page.
• Link to Facebook page.

```html
<!DOCTYPE html>
<html lang="en">
<head>
<meta charset="utf-8">
<title>Bramble Ridge Foot Clinic</title>
<link href="https://fonts.googleapis.com/css2?family=Lato:wght@400;700&family=Open+Sans:wght@700&family=Questrial&family=Raleway:wght@400;500;600;700&display=swap" rel="stylesheet">
<style>
:root{
  --orange:#f07023;
  --green:#86c440;
  --purple:#6b449b;
  --navy:#3a2e86;
  --ink:#111111;
  --text:#333333;
  --muted:#f5f5f5;
  --line:#c9c9c9;
  --night:#121c2a;
  --white:#ffffff;
}
*{box-sizing:border-box;margin:0;padding:0}
html,body{width:1200px;height:2236px;overflow:hidden}
body{position:relative;background:var(--white);font-family:'Raleway',sans-serif;color:var(--text)}
a{color:inherit;text-decoration:none}

/* header */
.site-header{position:absolute;top:0;left:0;width:1200px;height:130px;background:var(--white);box-shadow:0 2px 4px rgba(0,0,0,.35);z-index:2}
.brand{position:absolute;left:100px;top:36px;display:flex;align-items:center;gap:12px;font-family:'Raleway',sans-serif;font-weight:700;font-size:26px;color:var(--purple);line-height:1.1;width:230px}
.brand-dot{width:22px;height:22px;border-radius:50%;background:var(--purple);flex:none}
.top-contact{position:absolute;top:28px;right:100px;display:flex;gap:26px;font-family:'Raleway',sans-serif;font-weight:600;font-size:14px;color:var(--ink)}
.top-contact span{display:flex;align-items:center;gap:9px}
.chip{width:28px;height:28px;border-radius:50%;background:var(--green);display:flex;align-items:center;justify-content:center}
.main-nav{position:absolute;top:96px;left:450px;display:flex;gap:48px;font-family:'Raleway',sans-serif;font-weight:600;font-size:16px;color:var(--ink)}
.main-nav .active{color:var(--navy)}
.book-btn{position:absolute;top:86px;left:882px;width:218px;height:32px;background:var(--orange);color:var(--white);font-family:'Raleway',sans-serif;font-weight:600;font-size:13px;display:flex;align-items:center;justify-content:center;gap:10px}

/* hero */
.hero{position:absolute;top:130px;left:0;width:1200px;height:467px}
.hero-photo{position:absolute;inset:0;background:linear-gradient(100deg,#e8a24a 0%,#f2c56a 25%,#c98243 50%,#7a5a52 72%,#a2a7b0 100%)}
.hero-title{position:absolute;left:100px;top:212px;width:420px;font-family:'Open Sans',sans-serif;font-weight:700;font-size:30px;line-height:39px;color:var(--orange)}
.hero-dots{position:absolute;left:101px;top:343px;display:flex;gap:6px}
.hero-dots i{width:9px;height:9px;border-radius:50%;background:var(--orange)}
.hero-dots i.on{background:var(--ink)}

/* section headings */
.section-title{position:absolute;left:0;width:1200px;text-align:center;font-family:'Questrial',sans-serif;font-size:32px;color:var(--ink)}
.section-title em{font-style:normal;color:var(--orange)}
.section-title .g{color:var(--green)}
.rule{position:absolute;left:312px;width:576px;height:1px;background:var(--line)}
.rule::after{content:"";position:absolute;left:255px;top:-1px;width:34px;height:3px;background:var(--orange)}

/* welcome */
.welcome-text{position:absolute;left:100px;top:712px;width:1000px;text-align:center;font-size:14px;line-height:26px;color:var(--text)}
.read-more{position:absolute;left:544px;top:850px;width:110px;height:32px;background:var(--orange);border-radius:4px;color:var(--white);font-size:12px;font-weight:600;display:flex;align-items:center;justify-content:center}

/* treatments */
.treatments{position:absolute;top:926px;left:0;width:1200px;height:568px;background:var(--muted)}
.treat-intro{position:absolute;left:100px;top:105px;width:1000px;text-align:center;font-family:'Lato',sans-serif;font-size:17px;line-height:27px;color:var(--ink)}
.card{position:absolute;top:204px;width:231px;height:275px;background:var(--white);border-bottom:3px solid var(--green);text-align:center}
.card.orange{border-color:var(--orange)}
.card-icon{width:76px;height:76px;border-radius:50%;background:var(--green);margin:46px auto 0}
.card-icon.orange{background:var(--orange)}
.card h3{margin-top:38px;font-family:'Lato',sans-serif;font-weight:700;font-size:16px;color:var(--ink)}
.card p{margin-top:10px;padding:0 12px;font-family:'Lato',sans-serif;font-size:13px;line-height:21px;color:var(--ink)}
.card-more{position:absolute;left:92px;bottom:-3px;width:47px;height:24px;border-radius:24px 24px 0 0;background:var(--green);color:var(--white);font-size:22px;line-height:26px}
.card.orange .card-more{background:var(--orange)}
.slide-arrow{position:absolute;top:330px}

/* inquiry */
.inquiry{position:absolute;top:1494px;left:0;width:1200px;height:280px;background:var(--orange)}
.foot-mark{position:absolute;left:298px;top:40px;width:96px;height:200px;border-radius:48px;background:rgba(255,255,255,.18)}
.inquiry h2{position:absolute;left:100px;top:68px;font-family:'Raleway',sans-serif;font-weight:700;font-size:36px;color:var(--white)}
.inquiry-text{position:absolute;left:100px;top:136px;width:300px;font-size:13px;line-height:20px;color:var(--white)}
.form-label{position:absolute;left:460px;top:46px;font-weight:700;font-size:15px;color:var(--white)}
.field{position:absolute;width:308px;height:42px;background:var(--white);border-radius:2px;font-size:13px;color:#666;padding:0 13px;display:flex;align-items:center}
.submit{position:absolute;left:460px;top:186px;width:162px;height:42px;background:var(--ink);color:var(--white);font-weight:700;font-size:17px;display:flex;align-items:center;justify-content:center}

/* footer */
.site-footer{position:absolute;top:1774px;left:0;width:1200px;height:462px}
.footer-photo{position:absolute;inset:0;background:linear-gradient(180deg,#1b2a3c 0%,#111a27 45%,#20242c 75%,#0e141c 100%);border-top:3px solid #2f5f9a}
.info-col{position:absolute;top:44px;width:350px;text-align:center;color:var(--white);font-family:'Lato',sans-serif;font-weight:700;font-size:14px}
.info-line{position:relative;height:26px;margin-bottom:18px}
.info-line::before,.info-line::after{content:"";position:absolute;top:13px;width:120px;height:1px;background:var(--green)}
.info-line::before{left:25px}.info-line::after{right:25px}
.footer-brand{position:absolute;left:490px;top:155px;width:220px;display:flex;align-items:center;gap:12px;font-family:'Raleway',sans-serif;font-weight:700;font-size:30px;line-height:1.1;color:var(--white)}
.footer-brand .brand-dot{background:var(--white)}
.footer-nav{position:absolute;top:338px;left:0;width:1200px;display:flex;justify-content:center;gap:20px;font-family:'Lato',sans-serif;font-size:14px;color:var(--white)}
.footer-nav span+span::before{content:"•";margin-right:10px;color:#aaa}
.footer-bar{position:absolute;top:378px;left:0;width:1200px;height:1px;background:rgba(255,255,255,.15)}
.copyright{position:absolute;left:100px;top:412px;font-family:'Lato',sans-serif;font-size:14px;color:var(--white)}
.social{position:absolute;right:100px;top:400px;display:flex;gap:16px}
.social i{width:36px;height:36px;border-radius:50%;border:2px solid var(--white)}
</style>
</head>
<body>

<header class="site-header">
  <a class="brand" href="#"><span class="brand-dot"></span>Bramble Ridge Foot Clinic</a>
  <div class="top-contact">
    <span><i class="chip"><svg width="14" height="10" viewBox="0 0 14 10"><rect x="0.5" y="0.5" width="13" height="9" fill="none" stroke="#fff"/><path d="M0.5 0.5 7 6 13.5 0.5" fill="none" stroke="#fff"/></svg></i>info@brambleridgepodiatry.net</span>
    <span><i class="chip"><svg width="14" height="14" viewBox="0 0 24 24"><path fill="#fff" d="M6.6 10.8a15 15 0 0 0 6.6 6.6l2.2-2.2a1 1 0 0 1 1-.25 11.4 11.4 0 0 0 3.6.57 1 1 0 0 1 1 1V20a1 1 0 0 1-1 1A17 17 0 0 1 3 4a1 1 0 0 1 1-1h3.5a1 1 0 0 1 1 1c0 1.25.2 2.45.57 3.57a1 1 0 0 1-.25 1z"/></svg></i>(310) 555-0148</span>
  </div>
  <nav class="main-nav">
    <a class="active" href="#">home</a><a href="#">about us</a><a href="#">services</a><a href="#">contact us</a>
  </nav>
  <a class="book-btn" href="#"><svg width="18" height="18" viewBox="0 0 18 18"><rect x="1" y="3" width="14" height="13" fill="none" stroke="#fff" stroke-width="1.5"/><line x1="1" y1="7" x2="15" y2="7" stroke="#fff" stroke-width="1.5"/><circle cx="13" cy="13" r="4" fill="var(--orange)" stroke="#fff" stroke-width="1.5"/></svg>book an appointment</a>
</header>

<section class="hero">
  <div class="hero-photo" role="img" aria-label="Runner's legs in sports shoes on a sunlit mountain trail"></div>
  <h1 class="hero-title">Bramble Ridge Foot Clinic is a Podiatry clinic in the heart of Melbourne</h1>
  <div class="hero-dots"><i></i><i class="on"></i><i></i></div>
</section>

<section class="welcome">
  <h2 class="section-title" style="top:636px">welcome to <em>bramble ridge</em> foot <span class="g">clinic</span></h2>
  <div class="rule" style="top:692px"></div>
  <p class="welcome-text">Lorem ipsum dolor sit amet, consectetuer adipiscing elit, sed diam nonummy nibh euismod tincidunt ut laoreet dolore magna aliquam erat volutpat. Ut wisi enim ad minim veniam, quis nostrud exerci tation ullamcorper suscipit lobortis nisl ut aliquip ex ea commodo consequat. Duis autem vel eum iriure dolor in hendrerit in vulputate velit esse molestie consequat, vel illum dolore eu feugiat nulla facilisis at vero eros et accumsan et iusto odio dignissim qui blandit praesent luptatum zzril delenit augue duis dolore te feugait nulla facilisi.</p>
  <a class="read-more" href="#">read more</a>
</section>

<section class="treatments">
  <h2 class="section-title" style="top:34px">podiatry <em>treatments</em></h2>
  <div class="rule" style="top:86px"></div>
  <p class="treat-intro">Lorem ipsum dolor sit amet, consectetuer adipiscing elit, sed diam nonummy nibh euismod tincidunt ut laoreet dolore magna aliquam erat volutpat. Ut wisi enim ad minim veniam, quis nostrud exerci tation ullamcorper suscipit lobortis nisl ut</p>
  <svg class="slide-arrow" style="left:50px" width="14" height="22" viewBox="0 0 14 22"><path d="M11 2 3 11l8 9" fill="none" stroke="#8a8fb5" stroke-width="2"/></svg>
  <svg class="slide-arrow" style="left:1136px" width="14" height="22" viewBox="0 0 14 22"><path d="M3 2l8 9-8 9" fill="none" stroke="#8a8fb5" stroke-width="2"/></svg>
  <article class="card" style="left:100px"><div class="card-icon"></div><h3>treadmill analysis</h3><p>Duis autem vel eum iriure dolor in hendrerit in vulputate</p><span class="card-more">+</span></article>
  <article class="card orange" style="left:356px"><div class="card-icon orange"></div><h3>orthotis therapy</h3><p>Duis autem vel eum iriure dolor in hendrerit in vulputate</p><span class="card-more">+</span></article>
  <article class="card" style="left:613px"><div class="card-icon"></div><h3>callus</h3><p>Duis autem vel eum iriure dolor in hendrerit in vulputate</p><span class="card-more">+</span></article>
  <article class="card orange" style="left:869px"><div class="card-icon orange"></div><h3>heel pain</h3><p>Duis autem vel eum iriure dolor in hendrerit in vulputate</p><span class="card-more" style="background:var(--green)">+</span></article>
</section>

<section class="inquiry">
  <div class="foot-mark"></div>
  <h2>quick inquiry</h2>
  <p class="inquiry-text">Duis autem vel eum iriure dolormi opl inmokl hendi rerit in vulpu tateml velitm essemol mo molestiel conseqb uat, velmi illum dolor eokf no atn nulla more facilisis... [+]</p>
  <p class="form-label">please fill up bellow form</p>
  <div class="field" style="left:460px;top:83px">name</div>
  <div class="field" style="left:793px;top:83px">email</div>
  <div class="field" style="left:460px;top:135px">phone</div>
  <div class="field" style="left:793px;top:135px">message</div>
  <a class="submit" href="#">submit</a>
</section>

<footer class="site-footer">
  <div class="footer-photo" role="img" aria-label="Melbourne city skyline at night"></div>
  <div class="info-col" style="left:125px">
    <div class="info-line"><svg width="18" height="24" viewBox="0 0 18 24"><path d="M9 23C9 23 2 14 2 9a7 7 0 0 1 14 0c0 5-7 14-7 14z" fill="none" stroke="#fff" stroke-width="1.4"/><circle cx="9" cy="9" r="2.5" fill="none" stroke="#fff" stroke-width="1.4"/></svg></div>
    Suite 214/62 Larkin Street Melbourne 3000
  </div>
  <div class="info-col" style="left:425px">
    <div class="info-line"><svg width="24" height="24" viewBox="0 0 24 24"><path fill="none" stroke="#fff" stroke-width="1.4" d="M6.6 10.8a15 15 0 0 0 6.6 6.6l2.2-2.2a1 1 0 0 1 1-.25 11.4 11.4 0 0 0 3.6.57 1 1 0 0 1 1 1V20a1 1 0 0 1-1 1A17 17 0 0 1 3 4a1 1 0 0 1 1-1h3.5a1 1 0 0 1 1 1c0 1.25.2 2.45.57 3.57a1 1 0 0 1-.25 1z"/></svg></div>
    Phone: 1300 000 482
  </div>
  <div class="info-col" style="left:725px">
    <div class="info-line"><svg width="24" height="24" viewBox="0 0 24 24"><path d="M22 2 2 10l8 3 3 9z M10 13 22 2" fill="none" stroke="#fff" stroke-width="1.4" stroke-linejoin="round"/></svg></div>
    Email: info@brambleridgepodiatry.net
  </div>
  <div class="footer-brand"><span class="brand-dot"></span>Bramble Ridge Foot Clinic</div>
  <nav class="footer-nav"><span>home</span><span>about us</span><span>services</span><span>contact us</span></nav>
  <div class="footer-bar"></div>
  <p class="copyright">Copyright © 2016 Bramble Ridge Foot Clinic.&nbsp; All Right Reserved.</p>
  <div class="social"><i style="background:#3b5998"></i><i style="background:#0e76a8"></i><i style="background:#1da1f2"></i><i style="background:#dd4b39"></i></div>
</footer>

</body>
</html>
```